Upmarket Dessert Lounge needs a Business Card Design

We are an upmarket dessert lounge needing a business card to match our image.

We want something that is simple yet beautiful, feminine, classy, sophisticated and elegant. We want it to stand out and don't mind if it is bold.

The design should include our logo and colours of red or maroon with gold highlights. We don't mind if black is used.

Marlow & Quince

Target Market(s)

For those who like to indulge or treat themselves and give in to their temptations on good quality desserts.

Industry/Entity Type

Business

Requirements
Must have
• Must include our logo and our name

Marlow & Quince

M & Q

```html
<!DOCTYPE html>
<html lang="en">
<head>
<meta charset="utf-8">
<title>Marlow &amp; Quince — Business Card</title>
<link rel="stylesheet" href="https://fonts.googleapis.com/css2?family=Tinos:wght@400;700&display=swap">
<style>
  :root {
    --backdrop: #e9e4de;
    --card-white: #ffffff;
    --card-black: #050505;
    --maroon: #7a1a1e;
    --maroon-deep: #5e1014;
    --gold: #f2c99a;
    --ink: #333333;
    --paper-text: #ffffff;
  }
  * { box-sizing: border-box; margin: 0; padding: 0; }
  html, body { width: 1200px; height: 417px; overflow: hidden; }
  body {
    background: var(--backdrop);
    font-family: "Tinos", "Times New Roman", serif;
    position: relative;
  }
  .card {
    position: absolute;
    width: 516px;
    height: 294px;
    border-radius: 16px;
    overflow: hidden;
    box-shadow: 0 3px 10px rgba(0,0,0,0.25);
  }
  /* Front */
  .card-front { left: 41px; top: 57px; background: var(--card-white); }
  .card-front .swoosh { position: absolute; inset: 0; }
  .brand-mark {
    position: absolute;
    left: 24px; top: 108px;
    width: 210px;
    display: flex; align-items: center; gap: 8px;
    color: var(--maroon);
    font-size: 24px;
    font-weight: 400;
    white-space: nowrap;
  }
  .brand-dot {
    width: 12px; height: 12px; border-radius: 50%;
    background: var(--maroon); flex: none;
  }
  .holder {
    position: absolute; left: 326px; top: 56px;
    color: var(--maroon); font-size: 19px; font-weight: 700;
  }
  .holder .title { font-weight: 400; font-size: 15px; color: var(--ink); }
  .contacts {
    position: absolute; left: 325px; top: 96px;
    list-style: none; color: var(--ink); font-size: 13.5px;
  }
  .contacts li { display: flex; align-items: center; gap: 6px; height: 20.5px; }
  .contacts svg { width: 11px; height: 11px; fill: var(--maroon); flex: none; }
  .address {
    position: absolute; right: 24px; bottom: 14px;
    color: var(--paper-text); font-size: 14px;
  }
  /* Back */
  .card-back { left: 643px; top: 65px; background: var(--card-black); }
  .ornament-band {
    position: absolute; left: 0; right: 0; height: 38px;
    background: linear-gradient(180deg, #d9b083, var(--gold) 50%, #d9b083);
    opacity: 0.85;
  }
  .ornament-top { top: 0; }
  .ornament-bottom { bottom: 0; }
  .back-brand {
    position: absolute; left: 0; right: 0; top: 124px;
    text-align: center; color: var(--gold);
    font-size: 28px; font-weight: 400;
  }
  .back-web {
    position: absolute; left: 0; right: 0; top: 226px;
    text-align: center; color: var(--paper-text);
    font-size: 13px; letter-spacing: 2.4px;
  }
</style>
</head>
<body>

<section class="card card-front" aria-label="Business card front">
  <svg class="swoosh" viewBox="0 0 516 294" preserveAspectRatio="none" aria-hidden="true">
    <path d="M0,236 C150,282 380,262 516,176 L516,294 L0,294 Z" fill="var(--card-black)"/>
    <path d="M230,266 C360,250 460,212 516,180 L516,162 C455,205 360,242 230,266 Z" fill="var(--gold)"/>
    <path d="M0,226 C150,272 380,250 516,152" fill="none" stroke="var(--maroon)" stroke-width="6"/>
    <path d="M120,262 C300,262 440,215 516,166" fill="none" stroke="var(--card-black)" stroke-width="3"/>
  </svg>

  <div class="brand-mark"><span class="brand-dot"></span>Marlow &amp; Quince</div>

  <p class="holder">YOUR NAME, <span class="title">Title</span></p>

  <ul class="contacts">
    <li>
      <svg viewBox="0 0 12 12"><path d="M2.5 1 L4.5 1 L5.3 3.6 L4 4.6 C4.6 6 5.9 7.3 7.4 8 L8.4 6.7 L11 7.5 L11 9.5 C11 10.4 10.3 11 9.5 11 C5 11 1 7 1 2.5 C1 1.7 1.6 1 2.5 1 Z"/></svg>
      +44 20 7946 0321
    </li>
    <li>
      <svg viewBox="0 0 12 12"><path d="M3.5 0.5 H8.5 A1 1 0 0 1 9.5 1.5 V10.5 A1 1 0 0 1 8.5 11.5 H3.5 A1 1 0 0 1 2.5 10.5 V1.5 A1 1 0 0 1 3.5 0.5 Z M4 2 V8 H8 V2 Z"/></svg>
      +44 20 7946 0321
    </li>
    <li>
      <svg viewBox="0 0 12 12"><path d="M0.5 2.5 H11.5 V9.5 H0.5 Z" /><path d="M0.5 2.5 L6 7 L11.5 2.5" fill="none" stroke="#fff" stroke-width="1"/></svg>
      hello@marlowquince.com
    </li>
    <li>
      <svg viewBox="0 0 12 12"><circle cx="6" cy="6" r="5.5"/><path d="M0.5 6 H11.5" stroke="#fff" stroke-width="0.8"/></svg>
      www.marlowquince.com
    </li>
  </ul>

  <p class="address">00, Complex name City, State 000 000</p>
</section>

<section class="card card-back" aria-label="Business card back">
  <div class="ornament-band ornament-top" role="img" aria-label="Gold floral scroll border"></div>
  <p class="back-brand">Marlow &amp; Quince</p>
  <p class="back-web">www.marlowquince.com</p>
  <div class="ornament-band ornament-bottom" role="img" aria-label="Gold floral scroll border"></div>
</section>

</body>
</html>
```